Tolbek cards

I want a simple business card that pops.
Logo on one side.
On side two i want.
"Are you thinking about a new building on your property, or renovating an existing structure? Contact".....
Owners Name: Dale Whitacre
Owners Phone number: 610-555-0187
Address:4076 Copper Ridge RD, Marlow Falls, PA 17099
Committed to Quality, Service, and Integrity

```html
<!DOCTYPE html>
<html lang="en">
<head>
<meta charset="utf-8">
<title>Tolbek Builders LLC – Business Cards</title>
<link rel="stylesheet" href="https://fonts.googleapis.com/css2?family=Archivo:wght@400;500;700;800;900&display=swap">
<style>
  :root {
    --backdrop: #c4bea9;
    --card-light: #ece8e4;
    --brown-dark: #3d2a1f;
    --brown-deep: #2f2018;
    --tan: #8b7464;
    --tan-light: #a68f7c;
    --ink: #3b2a20;
    --white: #ffffff;
  }
  * { box-sizing: border-box; margin: 0; padding: 0; }
  html, body {
    width: 1200px; height: 988px; overflow: hidden;
    background: var(--backdrop);
    font-family: "Archivo", "Helvetica Neue", Arial, sans-serif;
  }
  .canvas { position: relative; width: 1200px; height: 988px; }
  .card {
    position: absolute; left: 220px; width: 760px; height: 434px;
    border-radius: 4px; overflow: hidden;
    box-shadow: 0 18px 40px rgba(60, 50, 30, 0.28);
  }
  /* Front side */
  .card-front {
    top: 40px; background: var(--card-light);
    display: flex; flex-direction: column; align-items: center; justify-content: center;
    color: var(--ink);
  }
  .brand-name {
    font-weight: 900; font-size: 104px; letter-spacing: 2px; line-height: 1;
    text-transform: uppercase; color: var(--brown-dark);
  }
  .brand-sub {
    margin-top: 8px; font-weight: 900; font-size: 30px; letter-spacing: 3px;
    text-transform: uppercase; color: var(--brown-dark);
  }
  .brand-rule {
    width: 60px; height: 2px; background: var(--brown-dark); margin: 22px 0 18px;
  }
  .brand-tagline {
    font-weight: 500; font-size: 15px; letter-spacing: 1px;
    text-transform: uppercase; color: var(--brown-dark);
  }
  /* Back side */
  .card-back { top: 514px; background: var(--card-light); }
  .back-quote {
    position: absolute; left: 42px; top: 36px; width: 470px;
    font-size: 29px; line-height: 1.2; color: var(--ink); font-weight: 400;
  }
  .back-quote strong { font-weight: 800; }
  .back-stripe {
    position: absolute; left: 0; right: 0; top: 230px; height: 8px;
    background: linear-gradient(90deg, var(--tan), var(--tan-light));
  }
  .back-band {
    position: absolute; left: 0; right: 0; top: 238px; bottom: 0;
    background: linear-gradient(180deg, var(--brown-dark), var(--brown-deep));
  }
  .role-tag {
    position: absolute; left: 42px; top: 200px; padding: 5px 12px;
    background: var(--tan); color: var(--white);
    font-size: 22px; font-weight: 400; letter-spacing: 0.5px;
  }
  .owner-name {
    position: absolute; left: 42px; top: 252px;
    color: var(--white); font-weight: 800; font-size: 64px; line-height: 0.98;
  }
  .contact-list {
    position: absolute; left: 470px; top: 262px; list-style: none;
    color: var(--card-light); font-size: 21px; line-height: 1.35;
  }
  .contact-item { display: flex; align-items: flex-start; gap: 10px; }
  .contact-icon { width: 18px; height: 18px; margin-top: 4px; flex: none; fill: var(--card-light); }
</style>
</head>
<body>
<main class="canvas">
  <section class="card card-front" aria-label="Card front">
    <div class="brand-name">Tolbek</div>
    <div class="brand-sub">Builders LLC</div>
    <div class="brand-rule"></div>
    <p class="brand-tagline">Committed to Quality, Service, and Integrity</p>
  </section>

  <section class="card card-back" aria-label="Card back">
    <p class="back-quote">"Are you <strong>thinking about a new building on your property</strong>, or renovating an existing structure? <strong>Contact</strong>" .....</p>
    <div class="back-stripe"></div>
    <div class="back-band"></div>
    <span class="role-tag">Owner</span>
    <h1 class="owner-name">Dale<br>Whitacre</h1>
    <ul class="contact-list">
      <li class="contact-item">
        <svg class="contact-icon" viewBox="0 0 24 24" aria-hidden="true"><path d="M6.6 10.8a15.1 15.1 0 0 0 6.6 6.6l2.2-2.2c.3-.3.7-.4 1-.2 1.1.4 2.3.6 3.6.6.6 0 1 .4 1 1V20c0 .6-.4 1-1 1A17 17 0 0 1 3 4c0-.6.4-1 1-1h3.5c.6 0 1 .4 1 1 0 1.3.2 2.5.6 3.6.1.3 0 .7-.2 1z"/></svg>
        <span>610-555-0187</span>
      </li>
      <li class="contact-item">
        <svg class="contact-icon" viewBox="0 0 24 24" aria-hidden="true"><path d="M12 2a7 7 0 0 0-7 7c0 5.2 7 13 7 13s7-7.8 7-13a7 7 0 0 0-7-7zm0 9.5A2.5 2.5 0 1 1 12 6.5a2.5 2.5 0 0 1 0 5z"/></svg>
        <span>4076 Copper Ridge RD,<br>Marlow Falls, PA 17099</span>
      </li>
    </ul>
  </section>
</main>
</body>
</html>
```